Business Card Design Project

Business Card
We are rebranding with a new logo
Industry/Entity Type
Business
Contact Information for Business Card
Dennis Morvale +61 487215963 dennis@quorv.com.au P.O. Box 872 Fernlow QLD 4309
Requirements
Must have
- Logo

```html
<!DOCTYPE html>
<html lang="en">
<head>
<meta charset="utf-8">
<title>Quorv International – Business Card</title>
<link rel="stylesheet" href="https://fonts.googleapis.com/css2?family=Nunito+Sans:wght@300;400;700;800&display=swap">
<style>
  :root {
    --backdrop: #d9d6d1;
    --card-white: #ececec;
    --orange: #e5602a;
    --orange-deep: #c64a1d;
    --charcoal: #1d1d21;
    --ink-light: #f2f2f2;
    --accent-blue: #3c8fd6;
  }
  * { box-sizing: border-box; margin: 0; padding: 0; }
  html, body {
    width: 1200px; height: 686px; overflow: hidden;
    background: var(--backdrop);
    font-family: "Nunito Sans", sans-serif;
  }
  .stage {
    width: 1200px; height: 686px;
    display: flex; align-items: center; justify-content: center;
  }
  .card {
    position: relative;
    width: 980px; height: 560px;
    background: var(--card-white);
    overflow: hidden;
    box-shadow: 0 10px 30px rgba(0,0,0,.25);
  }
  .card-shapes { position: absolute; inset: 0; }
  .brand {
    position: absolute; left: 62px; top: 70px;
    display: flex; align-items: center; gap: 14px;
    color: var(--charcoal);
    font-weight: 800; font-size: 30px; line-height: 1.05;
    letter-spacing: 2px; text-transform: uppercase;
  }
  .brand-mark {
    width: 26px; height: 26px; border-radius: 50%;
    background: var(--charcoal);
  }
  .identity {
    position: absolute; right: 130px; top: 118px; text-align: right;
    color: var(--ink-light);
  }
  .identity-name { font-size: 40px; letter-spacing: 1px; }
  .identity-name .first { font-weight: 800; }
  .identity-name .last { font-weight: 300; }
  .identity-role {
    margin-top: 4px; margin-right: 78px;
    color: var(--accent-blue); font-size: 18px; letter-spacing: 2px;
  }
  .contacts {
    position: absolute; right: 130px; top: 330px; text-align: right;
    color: var(--ink-light); font-weight: 400; letter-spacing: 2.5px;
  }
  .contact-group { margin-bottom: 14px; }
  .phones { font-size: 20px; line-height: 1.1; }
  .web { font-size: 22px; line-height: 1.1; }
  .address { font-size: 18px; line-height: 1.15; }
  .contact-icons {
    position: absolute; right: 14px; top: 330px;
    display: flex; flex-direction: column; gap: 42px; align-items: center;
  }
</style>
</head>
<body>
<main class="stage">
  <section class="card" aria-label="Business card for Dennis Morvale, Quorv International">
    <svg class="card-shapes" viewBox="0 0 980 560" width="980" height="560" aria-hidden="true">
      <polygon points="0,0 980,0 980,560 0,560" fill="var(--card-white)"/>
      <polygon points="0,0 470,0 510,130 455,410 0,225" fill="var(--orange)"/>
      <polygon points="380,0 470,0 500,60 430,50" fill="var(--card-white)"/>
      <polygon points="340,390 455,410 470,330" fill="var(--orange-deep)"/>
      <polygon points="470,0 980,0 980,560 140,560 455,410 510,130 490,70 510,0" fill="var(--charcoal)"/>
      <polygon points="960,0 980,0 980,560 900,560 900,250 960,200" fill="var(--orange)"/>
      <polygon points="935,0 960,0 960,200 900,250 900,260 935,230" fill="var(--charcoal)"/>
    </svg>

    <div class="brand">
      <span class="brand-mark"></span>
      <span class="brand-name">Quorv<br>International</span>
    </div>

    <div class="identity">
      <h1 class="identity-name"><span class="first">Dennis</span> <span class="last">Morvale</span></h1>
      <p class="identity-role">C.E.O</p>
    </div>

    <div class="contacts">
      <p class="contact-group phones">+61 487215963<br>+61 487330178</p>
      <p class="contact-group web">www.quorvgroup.com<br>dennis@quorv.com.au</p>
      <p class="contact-group address">P.O. Box 872 Fernlow QLD 4309<br>Harlow Park , Brisbane</p>
    </div>

    <div class="contact-icons" aria-hidden="true">
      <svg class="icon-phone" width="36" height="36" viewBox="0 0 36 36">
        <rect x="11" y="5" width="14" height="26" rx="3" fill="#fff"/>
        <rect x="13" y="8" width="10" height="18" fill="var(--accent-blue)"/>
        <circle cx="18" cy="28.5" r="1.2" fill="var(--accent-blue)"/>
      </svg>
      <svg class="icon-globe" width="36" height="36" viewBox="0 0 36 36">
        <circle cx="18" cy="18" r="12" fill="var(--accent-blue)" stroke="#fff" stroke-width="2"/>
        <ellipse cx="18" cy="18" rx="5" ry="12" fill="none" stroke="#fff" stroke-width="1.5"/>
        <line x1="6" y1="18" x2="30" y2="18" stroke="#fff" stroke-width="1.5"/>
        <line x1="8" y1="12" x2="28" y2="12" stroke="#fff" stroke-width="1.2"/>
        <line x1="8" y1="24" x2="28" y2="24" stroke="#fff" stroke-width="1.2"/>
      </svg>
      <svg class="icon-pin" width="36" height="36" viewBox="0 0 36 36">
        <path d="M18 4c-6 0-10 4.5-10 10 0 7 10 18 10 18s10-11 10-18c0-5.5-4-10-10-10z" fill="#fff"/>
        <circle cx="18" cy="14" r="4" fill="var(--accent-blue)"/>
      </svg>
    </div>
  </section>
</main>
</body>
</html>
```